Penfield Draft Works (PDWorks.net)

We need a Wordpress-based site designed for a client who provides writing and editing services for the IT industry. We have a wireframe complete for the homepage, but need all internal pages designed (based on homepage wireframe) and the entire site coded for WP.

Internal pages include: "Our Work" (with samples & testimonials); "Capabilities" (with sections to address "strategy", "coaching", "writing" and "editing"); "About Us"; and a Contact page.

Will provide all copywriting, writing samples, testimonials, and client logos.

We completely realize/acknowledge the subject matter is visually BORING! Anything at all that can be done to make it look visually appealing would be *great*! Stock photography is fine.

Please feel free to ask any questions whatsoever. Thanks for your time!

```html
<!DOCTYPE html>
<html lang="en">
<head>
<meta charset="utf-8">
<title>Penfield Draft Works</title>
<link rel="stylesheet" href="https://fonts.googleapis.com/css2?family=Comfortaa:wght@300;400&family=Montserrat:wght@400;500;600;800&family=Nothing+You+Could+Do&family=Playfair+Display:wght@700&display=swap">
<style>
:root{
  --red:#f41f0b;
  --ink:#111111;
  --cream:#e5e2cf;
  --grey:#c8c8c8;
  --line:#dddddd;
  --white:#ffffff;
  --text:#333333;
}
*{box-sizing:border-box;margin:0;padding:0}
html,body{width:1200px;height:3325px;overflow:hidden}
body{position:relative;background:var(--white);font-family:"Montserrat",sans-serif;color:var(--text)}
.abs{position:absolute}
.brand{font-family:"Playfair Display",serif;font-weight:700;font-size:25px;color:var(--red);white-space:nowrap}
.brand b{color:var(--ink);font-weight:700}

/* header */
.site-header{left:0;top:0;width:1200px;height:75px;background:var(--white)}
.site-header .brand{left:110px;top:20px}
.nav a{position:absolute;top:0;height:75px;line-height:75px;font-size:13px;color:var(--ink);text-decoration:none}
.nav .active{left:464px;width:62px;background:var(--red);color:var(--white);text-align:center}
.btn-solid{background:var(--red);color:var(--white);font-size:14px;font-weight:600;letter-spacing:1.5px;text-align:center}
.site-header .btn-solid{left:934px;top:19px;width:154px;height:38px;line-height:38px;border-radius:2px}

/* hero */
.hero{left:0;top:75px;width:1200px;height:642px;background:var(--cream)}
.hero-title{right:671px;top:128px;text-align:right;font-weight:800;font-size:54px;line-height:65px;color:var(--ink);letter-spacing:.5px}
.hero-title .hl{color:var(--red)}
.hero-script{left:118px;top:432px;font-family:"Nothing You Could Do",cursive;font-size:96px;line-height:110px;color:var(--red);white-space:nowrap;-webkit-text-stroke:1px var(--red)}
.hero-art{left:645px;top:241px;width:440px;height:290px;border-radius:6px;background:linear-gradient(135deg,#d9d5c1 0%,#b9b4a0 55%,#a39e89 100%)}

/* section headings */
.sec-head{left:0;width:1200px;text-align:center}
.sec-head h2{font-family:"Comfortaa",sans-serif;font-weight:400;font-size:34px;color:var(--ink)}
.sec-head p{font-family:"Nothing You Could Do",cursive;font-size:37px;color:var(--red);margin-top:4px;-webkit-text-stroke:.6px var(--red)}

/* service cards */
.card{top:928px;width:253px;height:280px;border:1px solid var(--line);background:var(--white);text-align:center}
.card svg{display:block;margin:30px auto 0}
.card h3{font-family:"Playfair Display",serif;font-weight:700;font-size:19px;color:var(--ink);margin-top:14px}
.card p{font-size:10.4px;line-height:20px;color:var(--ink);margin:12px 24px 0}
.card.featured{background:var(--red);border-color:var(--red)}
.card.featured h3,.card.featured p{color:var(--white)}

.btn-outline{border:1.5px solid var(--red);color:var(--red);font-size:14px;font-weight:600;letter-spacing:1.5px;text-align:center;background:var(--white);box-shadow:0 2px 4px rgba(0,0,0,.12)}

/* clients */
.client{top:1561px;height:170px;text-align:center;color:var(--ink)}
.client .name{font-weight:600;letter-spacing:3px}

/* work */
.work{top:1971px;width:313px;height:431px;background:var(--grey)}
.work .doc{position:absolute;left:34px;top:34px;width:245px;height:362px;box-shadow:0 6px 14px rgba(0,0,0,.3)}

/* cta */
.cta{top:2613px;height:420px}
.cta-contact{left:0;width:596px;background:linear-gradient(135deg,#f2361d 0%,#e8341c 50%,#f0522f 100%)}
.cta-news{left:604px;width:596px;background:linear-gradient(135deg,#2e2e2e 0%,#1f1f1f 60%,#2a2a2a 100%)}
.cta h2{position:absolute;top:115px;font-family:"Comfortaa",sans-serif;font-weight:300;font-size:35px;line-height:49px;color:var(--white)}
.cta .script{font-family:"Nothing You Could Do",cursive;font-size:40px;-webkit-text-stroke:.6px var(--white)}
.cta-contact h2{left:111px}
.cta-news h2{left:67px}
.cta .field{position:absolute;top:274px;height:37px;line-height:37px;background:var(--white);font-size:14px;font-weight:600;letter-spacing:1.5px}
.cta-contact .field{left:111px;width:185px;text-align:center;color:var(--red)}
.cta-news .field{left:67px;width:417px;padding-left:22px;color:var(--ink)}

/* footer */
.site-footer .brand{left:113px;top:3098px}
.info{top:3155px;font-size:14px;line-height:27px;color:var(--ink)}
.social{left:1009px;top:3181px;display:flex;gap:5px}
.social span{width:15px;height:15px;border-radius:50%;background:var(--ink)}
.bottom-bar{left:0;top:3264px;width:1200px;height:61px;background:#0b0b0b;color:var(--white);font-size:11px;font-weight:600;text-align:center;line-height:61px}
</style>
</head>
<body>

<header class="abs site-header">
  <div class="abs brand">Penfield Draft <b>Works</b></div>
  <nav class="nav">
    <a class="active" href="#">Home</a>
    <a style="left:553px" href="#">Our Work</a>
    <a style="left:654px" href="#">Capabilities</a>
    <a style="left:768px" href="#">About Us</a>
    <a style="left:867px" href="#">Blog</a>
  </nav>
  <div class="abs btn-solid">GET IN TOUCH</div>
</header>

<section class="abs hero">
  <h1 class="abs hero-title">COMMUNICATE<br>YOUR<br><span class="hl">EXPERTISE &amp;</span><br>YOU<br>CUSTOMER</h1>
  <div class="abs hero-script">Successes...</div>
  <div class="abs hero-art" role="img" aria-label="Engraved illustration of a hand writing with a pen"></div>
</section>

<div class="abs sec-head" style="top:794px">
  <h2>Text copy that explains in concise,</h2>
  <p>snappy terms the value you provide to customers.</p>
</div>

<div class="abs card" style="left:80px">
  <svg width="70" height="72" viewBox="0 0 70 72" fill="none" stroke="#111" stroke-width="2.5"><rect x="8" y="4" width="50" height="56" rx="3"/><rect x="15" y="11" width="36" height="42"/><circle cx="24" cy="22" r="4"/><circle cx="40" cy="36" r="4"/><path d="M28 22h8v10M24 26v14h12"/><path d="M52 44l10 14M4 66h62"/></svg>
  <h3>Strategy</h3>
  <p>Lorem Ipsum is simply dummy text of the printing and typesetting industry. Lorem Ipsum has been the industry's standard dummy text ever since the 1500s</p>
</div>
<div class="abs card featured" style="left:343px">
  <svg width="80" height="72" viewBox="0 0 80 72" fill="none" stroke="#fff" stroke-width="2.5"><rect x="14" y="8" width="62" height="46" rx="2"/><path d="M30 2v6M60 2v6M48 20h20M48 30h14"/><circle cx="28" cy="26" r="6"/><path d="M14 70V46q0-10 14-10l14-8M26 54v16M4 70h30"/></svg>
  <h3>Coaching</h3>
  <p>Lorem Ipsum is simply dummy text of the printing and typesetting industry. Lorem Ipsum has been the industry's standard dummy text ever since the 1500s</p>
</div>
<div class="abs card" style="left:605px">
  <svg width="72" height="72" viewBox="0 0 72 72" fill="none" stroke="#111" stroke-width="2.5"><path d="M62 4l6 6-34 40-10 4 4-10z"/><path d="M56 10l6 6"/><path d="M4 64q6-14 12-4t10-2 12 2 12-2"/></svg>
  <h3>Writing</h3>
  <p>Lorem Ipsum is simply dummy text of the printing and typesetting industry. Lorem Ipsum has been the industry's standard dummy text ever since the 1500s</p>
</div>
<div class="abs card" style="left:867px">
  <svg width="72" height="72" viewBox="0 0 72 72" fill="none" stroke="#111" stroke-width="4" stroke-linejoin="round"><path d="M36 12H10v52h52V38"/><path d="M56 6l10 10-28 28H28V34z"/></svg>
  <h3>Editing</h3>
  <p>Lorem Ipsum is simply dummy text of the printing and typesetting industry. Lorem Ipsum has been the industry's standard dummy text ever since the 1500s</p>
</div>

<div class="abs btn-outline" style="left:467px;top:1253px;width:265px;height:36px;line-height:33px">VIEW OUR CAPABILITIES</div>

<div class="abs sec-head" style="top:1412px">
  <h2>Neque porro quisquam</h2>
  <p>Neque porro quisquam Happy Clients</p>
</div>

<div class="abs client" style="left:110px;width:200px">
  <svg width="100" height="100" viewBox="0 0 100 100" style="margin-top:20px"><circle cx="50" cy="50" r="40" fill="none" stroke="#b8913a" stroke-width="2"/></svg>
  <div class="name" style="font-size:15px;color:#b8913a;margin-top:6px">HARLOW GROUP</div>
</div>
<div class="abs client" style="left:360px;width:200px">
  <svg width="50" height="50" viewBox="0 0 50 50" style="margin-top:30px"><circle cx="25" cy="25" r="23" fill="#a0177c"/></svg>
  <div class="name" style="font-size:18px;margin-top:20px">CRESTLINE CO</div>
</div>
<div class="abs client" style="left:605px;width:200px">
  <svg width="60" height="60" viewBox="0 0 60 60" style="margin-top:20px"><circle cx="30" cy="30" r="28" fill="#e8341c"/></svg>
  <div class="name" style="font-size:24px;font-weight:500;letter-spacing:1px;color:#c0311e;margin-top:14px">EMBERLY</div>
</div>
<div class="abs client" style="left:880px;width:220px">
  <svg width="80" height="80" viewBox="0 0 80 80" style="margin-top:2px"><rect x="0" y="0" width="80" height="80" fill="#0b0b0b"/></svg>
  <div class="name" style="font-size:30px;margin-top:12px">NORTHGATE</div>
</div>

<div class="abs sec-head" style="top:1848px">
  <h2>Text highlighting</h2>
  <p>the type of work you do</p>
</div>

<div class="abs work" style="left:111px"><div class="doc" role="img" aria-label="Sample letterhead with blue curved header" style="background:linear-gradient(160deg,#1d8fe0 0%,#ffffff 30%,#ffffff 85%,#1d8fe0 100%)"></div></div>
<div class="abs work" style="left:444px"><div class="doc" role="img" aria-label="Sample marketing brochure cover in navy and teal" style="background:linear-gradient(160deg,#ffffff 0%,#ffffff 30%,#1b3a7a 55%,#22b0c9 100%)"></div></div>
<div class="abs work" style="left:775px"><div class="doc" role="img" aria-label="Sample purple report cover with flowing lines" style="background:linear-gradient(160deg,#3a1a8a 0%,#8a2bc4 55%,#c042d8 100%)"></div></div>

<div class="abs btn-outline" style="left:506px;top:2451px;width:187px;height:36px;line-height:33px">VIEW OUR WORK</div>

<section class="abs cta cta-contact" role="img" aria-label="Red-toned photo of a hand writing with a pen">
  <h2>Feel free to contact us<br>with any questions.<br><span class="script">We're happy to help.</span></h2>
  <div class="field">GET IN TOUCH</div>
</section>
<section class="abs cta cta-news" role="img" aria-label="Dark-toned photo of a person working at a desk">
  <h2>Editorial inspiration<br>Delivered<br><span class="script">Straight to your Inbox.</span></h2>
  <div class="field">EMAIL ADDRESS</div>
</section>

<footer class="site-footer">
  <div class="abs brand">Penfield Draft <b>Works</b></div>
  <div class="abs info" style="left:113px">Address:<br>214 Maple Court, Fairview, Ohio, 43001.</div>
  <div class="abs info" style="left:480px;top:3151px">Phone:<br>(555) 014-2290</div>
  <div class="abs info" style="left:658px">Email Address:<br>hello@pdworks.net</div>
  <div class="abs info" style="left:1007px">Follow Us</div>
  <div class="abs social" aria-label="Social links"><span></span><span></span><span></span><span></span></div>
  <div class="abs bottom-bar">Penfield Draft Works © 2021 . All rights reserved.</div>
</footer>

</body>
</html>
```